Business card alterations

I have changed my business name from Brisa Laser Renewal Clinic to simply "Brisa Laser Clinic' and need this logo changed to reflect same

Brisa Laser Clinic
Est. 2004

I also need new business cards with above logo included and this attached card changed to the following.
Marianne Holcroft
Dermal Aesthetician
Grad Cert in Laser & IPL Treatments

I need at least one logo in less than 4mb so I can upload into my newsletter format so I can upload to newsletters, emails etc

Thanks
Mari

```html
<!DOCTYPE html>
<html lang="en">
<head>
<meta charset="utf-8">
<title>Brisa Laser Clinic – Business Card</title>
<link rel="stylesheet" href="https://fonts.googleapis.com/css2?family=Arimo:wght@400&family=Marcellus+SC&display=swap">
<style>
  :root {
    --brand-green: #0fa862;
    --brand-green-light: #13b36c;
    --band-grey: #e3e5e8;
    --paper: #ffffff;
    --ink-green: #0c9a57;
    --backdrop: #d9dadc;
  }
  * { margin: 0; padding: 0; box-sizing: border-box; }
  html, body {
    width: 1200px; height: 864px; overflow: hidden;
    background: var(--backdrop);
  }
  .business-card {
    position: absolute; left: 100px; top: 152px;
    width: 1000px; height: 560px;
    background: var(--paper);
    box-shadow: 0 18px 40px rgba(0,0,0,0.18);
    overflow: hidden;
  }
  .card-background { position: absolute; inset: 0; width: 1000px; height: 560px; }
  .card-text { position: absolute; white-space: nowrap; }
  .brand-name {
    left: 62px; top: 36px;
    font-family: "Marcellus SC", serif; font-size: 112px; line-height: 1;
    color: var(--paper);
  }
  .brand-sub {
    left: 70px; top: 166px; width: 300px; text-align: center;
    font-family: "Marcellus SC", serif; color: var(--paper);
    line-height: 1.25;
  }
  .brand-sub .clinic { font-size: 30px; display: block; }
  .brand-sub .established { font-size: 28px; display: block; }
  .holder-name {
    left: 545px; top: 62px;
    font-family: "Marcellus SC", serif; font-size: 31px; color: var(--paper);
    letter-spacing: 0.5px;
  }
  .holder-role {
    left: 547px; top: 108px;
    font-family: "Arimo", sans-serif; font-size: 23px; color: var(--paper);
  }
  .contact-line {
    font-family: "Arimo", sans-serif; font-size: 20px; color: var(--paper); line-height: 1.25;
  }
  .address { left: 612px; top: 216px; }
  .email { left: 612px; top: 286px; }
  .website {
    left: 250px; top: 348px;
    font-family: "Arimo", sans-serif; font-size: 23px; color: var(--paper);
  }
  .phone {
    left: 262px; top: 422px;
    font-family: "Arimo", sans-serif; font-size: 23px; color: var(--ink-green);
  }
  .qualification {
    left: 132px; top: 490px;
    font-family: "Arimo", sans-serif; font-size: 24px; color: var(--ink-green);
  }
  .icon-tile {
    position: absolute; width: 50px; height: 50px; border-radius: 7px;
    background: var(--paper);
    box-shadow: 0 2px 4px rgba(0,0,0,0.12);
    display: flex; align-items: center; justify-content: center;
  }
  .icon-web { left: 110px; top: 358px; }
  .icon-phone { left: 120px; top: 432px; }
  .contact-icon { position: absolute; }
  .icon-pin { left: 560px; top: 224px; }
  .icon-mail { left: 558px; top: 296px; }
</style>
</head>
<body>
  <div class="business-card">
    <svg class="card-background" viewBox="0 0 1000 560" aria-hidden="true">
      <defs>
        <linearGradient id="greenField" x1="0" y1="0" x2="1" y2="1">
          <stop offset="0" stop-color="var(--brand-green-light)"/>
          <stop offset="1" stop-color="var(--brand-green)"/>
        </linearGradient>
      </defs>
      <rect width="1000" height="560" fill="url(#greenField)"/>
      <path d="M0 400 L700 400 C775 400 790 300 870 282 C910 272 960 268 1000 266 L1000 560 L0 560 Z" fill="var(--band-grey)"/>
      <path d="M0 468 L820 468 C880 462 870 340 930 300 C950 288 975 282 1000 280 L1000 560 L0 560 Z" fill="var(--paper)"/>
    </svg>

    <div class="card-text brand-name">Brisa</div>
    <div class="card-text brand-sub">
      <span class="clinic">Brisa Laser Clinic</span>
      <span class="established">Est. 2004</span>
    </div>

    <div class="card-text holder-name">Marianne Holcroft</div>
    <div class="card-text holder-role">Dermal Aesthetician</div>

    <svg class="contact-icon icon-pin" width="22" height="28" viewBox="0 0 22 28" aria-hidden="true">
      <path d="M11 1C5.5 1 2 5 2 10c0 7 9 17 9 17s9-10 9-17c0-5-3.5-9-9-9z" fill="var(--paper)"/>
      <circle cx="11" cy="10" r="3.5" fill="var(--brand-green)"/>
    </svg>
    <div class="card-text contact-line address">58 Wattle Grove Road<br>Kensington SA 5068</div>

    <svg class="contact-icon icon-mail" width="22" height="16" viewBox="0 0 22 16" aria-hidden="true">
      <rect x="1" y="1" width="20" height="14" fill="var(--paper)"/>
      <path d="M1 1 L11 9 L21 1" fill="none" stroke="var(--brand-green)" stroke-width="1.5"/>
    </svg>
    <div class="card-text contact-line email">info@brisaclinic.com.au</div>

    <div class="icon-tile icon-web">
      <svg width="26" height="26" viewBox="0 0 26 26" aria-hidden="true">
        <g fill="none" stroke="var(--ink-green)" stroke-width="1.8">
          <circle cx="13" cy="13" r="11"/>
          <ellipse cx="13" cy="13" rx="5" ry="11"/>
          <path d="M2 13h22M4 7h18M4 19h18"/>
        </g>
      </svg>
    </div>
    <div class="card-text website">www.brisaclinic.com.au</div>

    <div class="icon-tile icon-phone">
      <svg width="26" height="24" viewBox="0 0 26 24" aria-hidden="true">
        <path d="M2 8c0-3 5-5 11-5s11 2 11 5v2h-6V7.5c-1.5-.6-3-.8-5-.8s-3.5.2-5 .8V10H2z" fill="var(--ink-green)"/>
        <path d="M6 11h14l3 10H3z" fill="var(--ink-green)"/>
        <circle cx="13" cy="16" r="2.6" fill="var(--paper)"/>
      </svg>
    </div>
    <div class="card-text phone">(08) 8127 4390</div>

    <div class="card-text qualification">Grad Cert in Laser &amp; IPL Treatments</div>
  </div>
</body>
</html>
```